Brookvane Consulting Business Card Design

Business Card Design for Brookvane Consulting. Brookvane Consulting is a boutique consultancy based in Atlanta, GA., that specializes in marketing strategy, organization planning, and leadership development. We provide solutions for small businesses and startups as well as Vantage 300 companies.

http://brookvaneconsulting.com/

Target Market(s)

We provide solutions for small businesses and startups as well as Vantage 300 companies.

Industry/Entity Type

Consulting

Contact Information for Business Card

Two sided business card with priority on contact information, logo, tag line (Inspiration to Dream More, Do More, Become More)

Colors

Designer to choose colors to be used in the design.

Requirements
Must have
• contact information, logo, tag line (Inspiration to Dream More, Do More, Become More)
• Simple no over communication.
Nice to have
• I would like to see different placements of logo and creative use of both sides of the card
Should not have
• Do not put too much information on the card.

```html
<!DOCTYPE html>
<html lang="en">
<head>
<meta charset="utf-8">
<title>Brookvane Consulting Business Card</title>
<link rel="stylesheet" href="https://fonts.googleapis.com/css2?family=Questrial&family=Mulish:ital,wght@1,800&display=swap">
<style>
  :root {
    --backdrop: #e6e6e4;
    --card: #1b1b1c;
    --card-back: #141415;
    --frame-line: #8a8a8a;
    --ink-white: #f4f4f4;
    --ink-grey: #a9a9a9;
    --ink-soft: #d6d6d6;
    --pattern-a: #2a2a2b;
    --pattern-b: #101011;
  }
  * { box-sizing: border-box; margin: 0; padding: 0; }
  html, body { width: 1200px; height: 960px; overflow: hidden; }
  body {
    background: var(--backdrop);
    position: relative;
    font-family: "Questrial", "Century Gothic", sans-serif;
  }
  .card {
    position: absolute;
    width: 600px;
    height: 341px;
    background: var(--card);
    overflow: hidden;
  }
  .card--front { left: 302px; top: 130px; }
  .card--back { left: 299px; top: 489px; background: var(--card-back); }

  .card__frame {
    position: absolute;
    inset: 14px 14px 14px 14px;
    border: 1px solid var(--frame-line);
  }
  .card__frame::after {
    content: "";
    position: absolute;
    inset: 3px;
    border: 1px solid var(--frame-line);
    opacity: .55;
  }

  .wordmark {
    position: absolute;
    color: var(--ink-white);
    text-align: center;
    line-height: 1;
  }
  .wordmark__name { display: block; }
  .wordmark__sub { display: block; letter-spacing: .08em; }
  .card--front .wordmark { left: 48px; top: 134px; width: 220px; }
  .card--front .wordmark__name { font-size: 40px; }
  .card--front .wordmark__sub { font-size: 18px; margin-top: 10px; }

  .contact {
    position: absolute;
    left: 295px;
    top: 112px;
    color: var(--ink-soft);
  }
  .contact__name {
    font-size: 21px;
    color: var(--ink-grey);
    font-weight: 400;
    letter-spacing: .01em;
    -webkit-text-stroke: .5px var(--ink-grey);
  }
  .contact__title { font-size: 16px; margin-top: 4px; color: var(--ink-soft); }
  .contact__list { list-style: none; margin-top: 11px; }
  .contact__item {
    display: flex;
    align-items: center;
    gap: 8px;
    font-size: 15px;
    height: 19px;
  }
  .contact__icon { width: 13px; height: 13px; fill: var(--ink-grey); flex: none; }

  .card__pattern {
    position: absolute;
    inset: 0;
    background:
      radial-gradient(ellipse at 50% 55%, var(--pattern-b) 0%, var(--pattern-b) 30%, transparent 70%),
      linear-gradient(180deg, var(--pattern-a), var(--card-back));
  }
  .card--back .wordmark { left: 0; width: 600px; top: 112px; }
  .card--back .wordmark__name { font-size: 58px; }
  .card--back .wordmark__sub { font-size: 22px; margin-top: 14px; }
  .tagline {
    position: absolute;
    left: 0;
    width: 600px;
    top: 272px;
    text-align: center;
    font-family: "Mulish", "Century Gothic", sans-serif;
    font-style: italic;
    font-weight: 800;
    font-size: 14px;
    line-height: 18px;
    color: var(--ink-white);
  }
</style>
</head>
<body>
  <section class="card card--front" aria-label="Business card front">
    <div class="card__frame"></div>
    <div class="wordmark">
      <span class="wordmark__name">Brookvane</span>
      <span class="wordmark__sub">CONSULTING</span>
    </div>
    <div class="contact">
      <h1 class="contact__name">DANIEL ASHER</h1>
      <p class="contact__title">Founder/Managing Director</p>
      <ul class="contact__list">
        <li class="contact__item">
          <svg class="contact__icon" viewBox="0 0 16 16" aria-hidden="true"><path d="M3.5 1l3 3-1.8 2a9 9 0 0 0 5.3 5.3l2-1.8 3 3-2 2C6.5 14.5 1.5 9.5 1.5 3z"/></svg>
          <span>555-014-2730</span>
        </li>
        <li class="contact__item">
          <svg class="contact__icon" viewBox="0 0 16 16" aria-hidden="true"><path d="M1 3h14v10H1z M1.5 3.5 8 9l6.5-5.5" stroke="#1b1b1c" stroke-width="1.2"/></svg>
          <span>daniel@brookvaneconsulting.com</span>
        </li>
        <li class="contact__item">
          <svg class="contact__icon" viewBox="0 0 16 16" aria-hidden="true"><circle cx="8" cy="8" r="7"/><path d="M1 8h14M8 1c-3 3.5-3 10.5 0 14M8 1c3 3.5 3 10.5 0 14" stroke="#1b1b1c" stroke-width="1" fill="none"/></svg>
          <span>brookvaneconsulting.com</span>
        </li>
      </ul>
    </div>
  </section>

  <section class="card card--back" aria-label="Business card back">
    <div class="card__pattern" role="img" aria-label="Dark repeating geometric pattern in charcoal tones"></div>
    <div class="wordmark">
      <span class="wordmark__name">Brookvane</span>
      <span class="wordmark__sub">CONSULTING</span>
    </div>
    <p class="tagline">Inspiration to Dream More<br>Do More, Become More</p>
  </section>
</body>
</html>
```